Whitcombe Business Card Design

The name of the business is Dario Whitcombe, CPA LLC
The service that we offer is Accounting, Tax & Consulting Services. I need it to have the following items:
Dario Whitcombe, Principal
Phone Number
Email Address
Physical Address

I have attached the company logo, one in black and one in white. Please provide a design in black background and the other in white background. Please include "Accounting, Tax & Consulting Services". I want the business card to be clean and very professional.

```html
<!DOCTYPE html>
<html lang="en">
<head>
<meta charset="utf-8">
<title>Dario Whitcombe, CPA LLC – Business Cards</title>
<link href="https://fonts.googleapis.com/css2?family=Montserrat:wght@500;600;700&family=Roboto:wght@300;400&display=swap" rel="stylesheet">
<style>
  :root {
    --backdrop: #2a2a2b;
    --card-dark: #1f2021;
    --card-dark-edge: #2b2c2e;
    --card-light: #ececec;
    --card-light-edge: #dcdcdc;
    --brand-red: #8e1316;
    --ink-dark: #2e2f31;
    --ink-light: #f2f2f2;
    --tag-grey: #7a7a7b;
    --body-grey: #3a3a3c;
  }
  * { box-sizing: border-box; margin: 0; padding: 0; }
  html, body {
    width: 1200px; height: 1138px; overflow: hidden;
    background: var(--backdrop);
  }
  .card {
    position: absolute;
    border-radius: 16px;
    box-shadow: 0 6px 14px rgba(0,0,0,0.45);
  }
  .card--front {
    left: 272px; top: 184px; width: 622px; height: 376px;
    background: linear-gradient(160deg, var(--card-dark) 0%, var(--card-dark-edge) 100%);
  }
  .card--front .brand-mark {
    position: absolute; left: 271px; top: 112px;
    width: 80px; height: 80px; background: var(--brand-red);
  }
  .card--front .brand-text {
    position: absolute; left: 0; right: 0; top: 215px;
    text-align: center;
  }
  .wordmark {
    font-family: 'Montserrat', sans-serif;
    font-weight: 600;
    text-transform: uppercase;
    white-space: nowrap;
  }
  .card--front .wordmark { color: var(--ink-light); font-size: 24px; letter-spacing: 0.5px; line-height: 28px; }
  .tagline {
    font-family: 'Montserrat', sans-serif;
    font-weight: 600;
    text-transform: uppercase;
    color: var(--tag-grey);
    white-space: nowrap;
  }
  .card--front .tagline { font-size: 17px; letter-spacing: 3.1px; margin-top: 2px; }
  .services {
    font-family: 'Roboto', sans-serif;
    font-weight: 400;
    white-space: nowrap;
  }
  .card--front .services { color: #a9a9ab; font-size: 13px; letter-spacing: 0.6px; margin-top: 10px; }

  .card--back {
    left: 274px; top: 606px; width: 619px; height: 375px;
    background: linear-gradient(180deg, var(--card-light) 0%, var(--card-light-edge) 100%);
  }
  .card--back .brand-block { position: absolute; left: 36px; top: 52px; }
  .card--back .wordmark { color: var(--ink-dark); font-size: 19.6px; letter-spacing: 0.3px; line-height: 24px; }
  .card--back .tagline { font-size: 14.5px; letter-spacing: 2.3px; margin-top: 1px; }
  .card--back .services { color: var(--body-grey); font-size: 12.5px; letter-spacing: 0.4px; margin-top: 8px; }
  .card--back .brand-mark {
    position: absolute; left: 36px; top: 248px;
    width: 96px; height: 96px; background: var(--ink-dark);
  }

  .contact {
    position: absolute; right: 35px; top: 150px;
    text-align: right;
    font-family: 'Roboto', sans-serif;
    color: var(--body-grey);
  }
  .contact__name {
    font-family: 'Montserrat', sans-serif; font-weight: 700;
    font-size: 18.5px; color: var(--brand-red); text-transform: uppercase;
    letter-spacing: 0.3px;
  }
  .contact__role { font-size: 16px; font-weight: 400; margin-top: 1px; }
  .contact__address { font-size: 15.5px; font-weight: 300; line-height: 24px; margin-top: 32px; }
  .contact__line {
    display: flex; justify-content: flex-end; align-items: center;
    font-size: 15.5px; font-weight: 300; height: 24px;
  }
  .contact__address + .contact__line { margin-top: 3px; }
  .contact__icon { width: 14px; height: 14px; margin-left: 9px; fill: var(--brand-red); }
</style>
</head>
<body>
  <section class="card card--front">
    <div class="brand-mark"></div>
    <div class="brand-text">
      <div class="wordmark">Dario Whitcombe, CPA, LLC</div>
      <div class="tagline">Certified Public Accountant</div>
      <div class="services">Accounting, Tax &amp; Consulting Services</div>
    </div>
  </section>

  <section class="card card--back">
    <div class="brand-block">
      <div class="wordmark">Dario Whitcombe, CPA, LLC</div>
      <div class="tagline">Certified Public Accountant</div>
      <div class="services">Accounting, Tax &amp; Consulting Services</div>
    </div>

    <div class="brand-mark"></div>

    <div class="contact">
      <div class="contact__name">Dario Whitcombe</div>
      <div class="contact__role">Principal</div>
      <div class="contact__address">4180, Larkfield Avenue, Brookmere,<br>Eastvale County, US 284016</div>
      <div class="contact__line">555-014-2290
        <svg class="contact__icon" viewBox="0 0 16 16" aria-hidden="true"><path d="M1 5c0-2 3-3 7-3s7 1 7 3v1.5h-3.5V5h-7v1.5H1z"/><path d="M4 8l1.5-2h5L12 8v5H4z"/></svg>
      </div>
      <div class="contact__line">dw@dariowhitcombellc.com
        <svg class="contact__icon" viewBox="0 0 16 16" aria-hidden="true"><path d="M1 3h14v10H1z"/><path d="M1 3l7 6 7-6" fill="none" stroke="#ececec" stroke-width="1.4"/><path d="M1 13l5-5M15 13l-5-5" stroke="#ececec" stroke-width="1.2"/></svg>
      </div>
      <div class="contact__line">www.dariowhitcombellc.com
        <svg class="contact__icon" viewBox="0 0 16 16" aria-hidden="true"><circle cx="8" cy="8" r="7"/><g fill="none" stroke="#ececec" stroke-width="0.9"><ellipse cx="8" cy="8" rx="3" ry="7"/><path d="M1 8h14M2.5 4.5h11M2.5 11.5h11"/></g></svg>
      </div>
    </div>
  </section>
</body>
</html>
```